Brightway Haul & Upkeep Services, are a company that offers a 'one stop shop' pre-move clean up a

I have already selected a logo which I would like on the front of the business cards along with phone numbers, web address and email which are:
0487650392
www.brightwayhaul.com.au
brightwayhaulandupkeep@mailbox.example

On the back of the card I would like to list some of the types of service we offer (clean - move - repairs/maintenance) which are:
CLEAN - windows, gutters, solar panels, driveways/paths, carpets.
MOVE - Small/medium size house/office moves, large item pick-up & delivery, yard clean-up and removal.
General maintenance and repairs.

I would like the blue logo on a gray background.

Thanks

```html
<!DOCTYPE html>
<html lang="en">
<head>
<meta charset="utf-8">
<title>Brightway Haul &amp; Upkeep Services – Business Cards</title>
<link rel="stylesheet" href="https://fonts.googleapis.com/css2?family=Open+Sans:wght@400;600;700;800&display=swap">
<style>
  :root {
    --stage: #e9e7e4;
    --card-light: #f2f2f2;
    --card-mid: #c9c9c9;
    --card-dark: #a9a9a9;
    --brand-blue: #2a72bd;
    --ink: #2b2b2b;
    --ink-soft: #4a4a4a;
    --rule: #ffffff;
  }
  * { box-sizing: border-box; margin: 0; padding: 0; }
  html, body { width: 1200px; height: 805px; overflow: hidden; }
  body {
    background: var(--stage);
    font-family: "Open Sans", Arial, sans-serif;
    position: relative;
  }
  .card {
    position: absolute;
    width: 560px;
    height: 320px;
    border-radius: 4px;
    overflow: hidden;
    background: radial-gradient(ellipse at 45% 35%, var(--card-light) 0%, var(--card-mid) 60%, var(--card-dark) 100%);
    box-shadow: 0 10px 24px rgba(0,0,0,0.25);
  }
  .card--front { left: 40px; top: 110px; }
  .card--back { left: 600px; top: 375px; }

  .brand-name {
    color: var(--brand-blue);
    font-weight: 800;
    text-transform: uppercase;
    line-height: 1.05;
    letter-spacing: 0.5px;
  }
  .card--front .brand-name {
    position: absolute;
    left: 60px;
    top: 34px;
    font-size: 36px;
  }
  .card--front .brand-name span { display: block; }

  .front-wave { position: absolute; left: 0; top: 0; width: 560px; height: 320px; }

  .contact {
    position: absolute;
    left: 0; top: 0;
    width: 560px; height: 320px;
    font-size: 12px;
    color: var(--ink-soft);
  }
  .contact__phone {
    position: absolute; left: 130px; top: 180px;
    display: flex; align-items: center; gap: 6px;
  }
  .contact__divider {
    position: absolute; left: 262px; top: 130px;
    width: 1px; height: 80px; background: var(--rule);
  }
  .contact__list {
    position: absolute; left: 280px; top: 136px;
    list-style: none;
  }
  .contact__list li { display: flex; align-items: center; gap: 7px; margin-bottom: 12px; white-space: nowrap; }
  .icon { width: 12px; height: 12px; flex: none; }

  .card--back .brand-name {
    position: absolute;
    left: 0; top: 42px; width: 560px;
    text-align: center;
    font-size: 36px;
  }
  .services {
    position: absolute; left: 0; top: 150px; width: 560px;
    text-align: center;
  }
  .services__title {
    color: var(--brand-blue);
    font-size: 22px;
    font-weight: 600;
    letter-spacing: 6px;
    margin-bottom: 8px;
  }
  .services__list {
    list-style: none;
    color: var(--ink);
    font-size: 19px;
    font-weight: 600;
    line-height: 1.3;
  }
  .services__item::before { content: "• "; color: var(--brand-blue); }
  .services__row { display: flex; justify-content: center; gap: 22px; }
</style>
</head>
<body>

  <section class="card card--front" aria-label="Business card front">
    <h1 class="brand-name"><span>Brightway Haul</span><span>&amp; Upkeep Services</span></h1>

    <svg class="front-wave" viewBox="0 0 560 320" aria-hidden="true">
      <path d="M0 292 C 170 302, 390 262, 560 205 L560 320 L0 320 Z" fill="var(--brand-blue)"/>
      <path d="M0 287 C 170 297, 390 257, 560 200" fill="none" stroke="#1a1a1a" stroke-width="3"/>
    </svg>

    <div class="contact">
      <div class="contact__phone">
        <svg class="icon" viewBox="0 0 12 12" aria-hidden="true"><circle cx="6" cy="6" r="5.5" fill="var(--brand-blue)"/><path d="M4 3.2 L5 3 L5.6 4.6 L5 5.1 Q5.6 6.5 6.9 7 L7.4 6.4 L9 7 L8.8 8 Q6 8.6 3.9 5.6 Q3.6 4.2 4 3.2 Z" fill="#fff"/></svg>
        <span>0487650392</span>
      </div>
      <div class="contact__divider"></div>
      <ul class="contact__list">
        <li>
          <svg class="icon" viewBox="0 0 12 12" aria-hidden="true"><circle cx="6" cy="6" r="5.5" fill="var(--brand-blue)"/><rect x="3" y="4" width="6" height="4.2" fill="#fff"/><path d="M3 4 L6 6.4 L9 4" fill="none" stroke="var(--brand-blue)" stroke-width="0.8"/></svg>
          <span>brightwayhaulandupkeep@mailbox.example</span>
        </li>
        <li>
          <svg class="icon" viewBox="0 0 12 12" aria-hidden="true"><circle cx="6" cy="6" r="5.5" fill="var(--brand-blue)"/><circle cx="6" cy="6" r="3.2" fill="none" stroke="#fff" stroke-width="0.8"/><path d="M2.8 6 H9.2 M6 2.8 V9.2" stroke="#fff" stroke-width="0.8"/></svg>
          <span>www.brightwayhaul.com.au</span>
        </li>
      </ul>
    </div>
  </section>

  <section class="card card--back" aria-label="Business card back">
    <h2 class="brand-name">Brightway Haul<br>&amp; Upkeep Services</h2>
    <div class="services">
      <p class="services__title">Services we offer</p>
      <ul class="services__list">
        <li class="services__row"><span class="services__item">Clean</span><span class="services__item">Move</span></li>
        <li><span class="services__item">General maintenance and repairs.</span></li>
      </ul>
    </div>
  </section>

</body>
</html>
```